Bold, Modern, Clean "Kestrelwaymassage.com" website

Why we stand out?
We are a male and female mobile massage team. Our names are Paul and Lina. 
Kestrel Way is a Seattle based mobile massage service. Our massage is offered to the community with a goal of facilitating balance within each individual. We specialize in integrated Pain management, and sports/medical massage therapy. Every client's first assessment is attended by our male and female massage therapist team. Depending on the goals identified for an individual determines which therapist will be assigned to provide treatment, if not both.

Our passion...
Here at Kestrel Way, we have a great passion for Postural Resoration and how it is integrated into an individual's Massage treatment. We pride ourselves in being natural facilitators of healing, which takes the ego of the therapist out of the client's healing process. We strive to deliver the best massage possible by including modalities such as Neuromuscular, Myofascial release, spontaneous muscle release, postural restoration, orthopedic, and medical massage.

Our education...

We are both Graduates of Venmora, school of massage therapy. We have continuing education in medical massage, myofacial release, trigger point therapy, postural restoration, anatomy, and spontaneous muscle release. Lina is also a Certified Yoga Instructor, which amplifies her experience with flexibility and strength as it pertains to each individual. Paul's passion is Massage, stretching, and strength training to encourage postural restoration and realignment.

Our rates-

Our rates are $75/ 60 minutes, $95/ 90 minutes, and $120/ 120 minutes.

Education-
Both Lina and I worked as behavioral health professionals that specialized in life skills mentoring for youth who had experienced different types of trauma. This led us both to want to help others in a different environment, where individuals can be empowered to take responsibility over their own healing. To us, massage is a type of manipulation physical therapy, that encourages healing on many levels.

Advice to any massage client-
The most important thing to 'us', as Licenced providers is to get you on to our table to show you our skills. But a good therapist never forgets that it's not about what we do for you, but what we can facilitate for you. Your health and healing has nothing to do with us. It is yours, not ours. Identify what your goals are with any Therapist, and know what the end looks like. Progress should be tangible, such as range of motion, and decreased pain.

Lina and Paul at Kestrel Way are awesome! I recently had open heart surgery, and Lina worked on me to increase my range of motion while helping with the pinched nerve from my arm being in the same position for so long during my surgery. My wife drives a lot for work, and Paul has helped decrease her neck and lower back pain immensely. They are seriously the best therapists I have ever worked with. I would recommend them to anyone who needs anything from stress relief to a medical massage treatment. They are professional, up beat, easy going, and always on time. And, I love that they meet us where ever we like! We did a staycation recently, where they came to our hotel to give us relaxation massages. Although usually they come to our home, where we focus on pain related issues. We will continue to work with them for a long, long time.

Target Market(s)

Mobile massage therapy clients

Industry/Entity Type

Massage Therapy

Coding

Coded - Design and coding required

Number of Pages Required

1 page

Font styles to use
Serif
Sans Serif

Requirements
Must have
• Please add or remove any information that would help the presentation of our website. Our logo is posted below, please include into the website.
• Please include a contact field that includes, kestrelwaymassage@fernmail.net,
• (206) 555-0148
• We have also included our own stock photos, as well as a photo of Paul and Lina. Please include a cropped photo of both massage therapists.

```html
<!DOCTYPE html>
<html lang="en">
<head>
<meta charset="utf-8">
<title>Kestrel Way Mobile Massage</title>
<link href="https://fonts.googleapis.com/css2?family=Comfortaa:wght@700&family=Montserrat:wght@400;500;600&family=Roboto:wght@400&display=swap" rel="stylesheet">
<style>
:root{
  --blue:#0a24b4;
  --blue-deep:#0526b5;
  --teal:#19d9c9;
  --ink:#1b1b1b;
  --grey-text:#6b6b6b;
  --panel:#f1f1f1;
  --rule:#bdbdbd;
  --white:#ffffff;
}
*{margin:0;padding:0;box-sizing:border-box}
html,body{width:1200px;height:2917px;overflow:hidden;background:var(--white)}
body{position:relative;font-family:"Montserrat",Arial,sans-serif;color:var(--ink)}
.abs{position:absolute}
.section{position:absolute;left:0;width:1200px;overflow:hidden}
.heading{position:absolute;left:0;width:1200px;text-align:center;font-family:"Comfortaa",Arial,sans-serif;font-weight:700;font-size:40px;color:var(--blue);line-height:1}
.rule{position:absolute;left:424px;width:354px;height:1px;background:var(--rule)}
.body-copy{position:absolute;left:0;width:1200px;text-align:center;font-size:14px;line-height:29px}
.read-more{position:absolute;left:0;width:1200px;text-align:center;font-family:Arial,sans-serif;font-weight:700;font-size:19px;color:var(--blue);text-decoration:underline}

/* nav */
.site-nav{position:absolute;top:0;left:0;width:1200px;height:56px;background:rgba(40,40,40,.72);z-index:3}
.site-nav a{position:absolute;top:0;height:56px;line-height:58px;color:var(--white);font-size:14.5px;font-weight:600;text-decoration:none;text-align:center}
.site-nav a.active{background:var(--teal);color:var(--ink)}

/* hero */
.hero{top:0;height:677px;background:linear-gradient(100deg,#4b2a1f 0%,#b98f77 25%,#d9b5a2 45%,#e9d6c3 65%,#c8b67c 85%,#8f8a3c 100%)}
.hero-photo{position:absolute;inset:0;background:
  radial-gradient(ellipse 420px 260px at 600px 260px,rgba(246,222,205,.85),rgba(246,222,205,0) 70%),
  radial-gradient(ellipse 300px 220px at 1040px 180px,rgba(232,224,204,.9),rgba(232,224,204,0) 70%),
  radial-gradient(ellipse 360px 160px at 420px 620px,rgba(40,32,30,.75),rgba(40,32,30,0) 70%),
  radial-gradient(ellipse 260px 240px at 120px 330px,rgba(70,38,26,.7),rgba(70,38,26,0) 70%),
  radial-gradient(ellipse 240px 200px at 1160px 80px,rgba(170,190,70,.6),rgba(170,190,70,0) 70%)}
.brand-badge{position:absolute;left:497px;top:193px;width:206px;height:206px;border-radius:50%;background:var(--blue)}
.brand-name{position:absolute;left:497px;top:193px;width:206px;height:206px;display:flex;align-items:center;justify-content:center;text-align:center;font-family:"Montserrat",sans-serif;font-weight:600;font-size:27px;line-height:1.15;color:var(--white)}
.carousel-dot{position:absolute;left:594px;top:632px;width:12px;height:12px;border-radius:50%;background:var(--blue)}

/* who */
.who{top:677px;height:366px;background:var(--panel);border-top:2px solid #2a2a2a}
.team-photo{position:absolute;left:0;top:0;width:190px;height:366px;background:linear-gradient(90deg,rgba(120,104,98,1) 0%,rgba(150,136,128,.85) 60%,rgba(241,241,241,0) 100%)}

/* what */
.what{top:1043px;height:529px;background:linear-gradient(120deg,#f7efed 0%,#ffffff 35%,#eceae9 60%,#ffffff 100%)}
.service{position:absolute;top:0;width:260px;text-align:center}
.service-title{position:absolute;top:396px;left:0;width:100%;font-size:16px;font-weight:500;color:var(--ink)}
.service-text{position:absolute;top:430px;left:0;width:100%;font-family:"Roboto",sans-serif;font-size:14px;line-height:21px;color:var(--grey-text)}
.divider{position:absolute;top:202px;width:1px;height:165px;background:#cfcfcf}
.service-icon{position:absolute;width:178px;height:178px;top:193px}

/* education */
.education{top:1572px;height:344px;background:#f3f3f3}

/* rates */
.rates{top:1916px;height:364px;background:linear-gradient(90deg,#1d1d1d 0%,#3a3835 40%,#4b4742 70%,#2b2a28 100%)}
.rates .heading{color:var(--white);font-family:"Montserrat",sans-serif;font-weight:500}
.rate-price{position:absolute;width:132px;text-align:center;color:var(--white);font-size:18px;font-weight:600;line-height:24px}

/* testimonials */
.testimonials{top:2280px;height:346px;background:var(--white)}
.date{position:absolute;left:119px;top:193px;width:136px;text-align:center;font-size:14px;line-height:24px;color:var(--ink)}
.quote{position:absolute;left:282px;top:150px;width:805px;font-size:14px;line-height:26px}
.author{position:absolute;left:282px;top:270px;font-size:16px;font-weight:600}

/* footer */
.site-footer{top:2626px;height:291px;background:var(--blue-deep);overflow:visible}
.contact-text{position:absolute;top:81px;color:var(--white);font-size:15px}
.footer-nav{position:absolute;top:166px;left:0;width:1200px;display:flex;justify-content:center;color:var(--white);font-size:14px;font-weight:600}
.footer-nav span{padding:0 30px}
.footer-nav .sep{padding:0}
.footer-rule{position:absolute;left:78px;top:217px;width:1044px;height:1px;background:#2f66e8}
.copyright{position:absolute;top:243px;left:0;width:1200px;text-align:center;font-size:13px;color:#0b0b0b}
</style>
</head>
<body>

<nav class="site-nav">
  <a class="active" href="#" style="left:228px;width:95px">Home</a>
  <a href="#" style="left:335px;width:90px">About us</a>
  <a href="#" style="left:455px;width:135px">Our Passion</a>
  <a href="#" style="left:600px;width:100px">Education</a>
  <a href="#" style="left:730px;width:100px">Testimonial</a>
  <a href="#" style="left:855px;width:105px">Contact Us</a>
</nav>

<header class="section hero">
  <div class="hero-photo" role="img" aria-label="Photo of a woman relaxing during a facial massage with an orchid, candle and hot stones"></div>
  <div class="brand-badge"></div>
  <div class="brand-name">Kestrel<br>Way</div>
  <span class="carousel-dot"></span>
</header>

<section class="section who">
  <div class="team-photo" role="img" aria-label="Cropped photo of the massage therapist team"></div>
  <h2 class="heading" style="top:62px">Who We Are</h2>
  <div class="rule" style="top:121px"></div>
  <p class="body-copy" style="top:143px">We are a male and female mobile massage team. Our names are Paul and Lina.<br>Kestrel Way is a Seattle based mobile massage service. Our massage is offered to the community with a goal of<br>facilitating balance within each individual. We specialize in integrated Pain management, and sports/medical<br>massage therapy. Every client's first assessment is attended by our male and female massage therapist team.</p>
  <a class="read-more" style="top:283px">READ MORE</a>
</section>

<section class="section what">
  <div class="abs" role="img" aria-label="Soft background photo of a back massage" style="inset:0"></div>
  <h2 class="heading" style="top:55px">What We Do</h2>
  <div class="rule" style="top:115px"></div>
  <p class="body-copy" style="top:125px">We strive to deliver the best massage possible by including modalities</p>

  <svg width="0" height="0" class="abs" aria-hidden="true">
    <defs>
      <radialGradient id="ring" cx="50%" cy="50%" r="50%">
        <stop offset="0.72" stop-color="#0d3fd0"/>
        <stop offset="0.86" stop-color="#22c8ee"/>
        <stop offset="0.95" stop-color="#6fe6f6"/>
        <stop offset="1" stop-color="#d6f8fc"/>
      </radialGradient>
      <radialGradient id="core" cx="50%" cy="35%" r="65%">
        <stop offset="0" stop-color="#25b8f0"/>
        <stop offset="0.6" stop-color="#1060e0"/>
        <stop offset="1" stop-color="#0a2cc0"/>
      </radialGradient>
    </defs>
  </svg>
  <svg class="service-icon" style="left:115px" viewBox="0 0 178 178" role="img" aria-label="Neuromuscular icon"><circle cx="89" cy="89" r="89" fill="url(#ring)"/><circle cx="89" cy="89" r="66" fill="url(#core)"/><circle cx="89" cy="89" r="55" fill="none" stroke="#fff" stroke-width="1.5"/></svg>
  <svg class="service-icon" style="left:380px" viewBox="0 0 178 178" role="img" aria-label="Spontaneous muscle release icon"><circle cx="89" cy="89" r="89" fill="url(#ring)"/><circle cx="89" cy="89" r="66" fill="url(#core)"/><circle cx="89" cy="89" r="55" fill="none" stroke="#fff" stroke-width="1.5"/></svg>
  <svg class="service-icon" style="left:646px" viewBox="0 0 178 178" role="img" aria-label="Postural restoration icon"><circle cx="89" cy="89" r="89" fill="url(#ring)"/><circle cx="89" cy="89" r="66" fill="url(#core)"/><circle cx="89" cy="89" r="55" fill="none" stroke="#fff" stroke-width="1.5"/></svg>
  <svg class="service-icon" style="left:911px" viewBox="0 0 178 178" role="img" aria-label="Medical massage icon"><circle cx="89" cy="89" r="89" fill="url(#ring)"/><circle cx="89" cy="89" r="66" fill="url(#core)"/><circle cx="89" cy="89" r="55" fill="none" stroke="#fff" stroke-width="1.5"/></svg>
  <span class="divider" style="left:336px"></span>
  <span class="divider" style="left:603px"></span>
  <span class="divider" style="left:866px"></span>

  <div class="service" style="left:74px"><h3 class="service-title">Neuromuscular</h3><p class="service-text">Lorem ipsum dolor sit amet,<br>consectetur adipiscing elit,send.</p></div>
  <div class="service" style="left:339px"><h3 class="service-title">Spontaneous Muscle Release</h3><p class="service-text">Lorem ipsum dolor sit amet,<br>consectetur adipiscing elit,send.</p></div>
  <div class="service" style="left:605px"><h3 class="service-title" style="font-weight:400">Postural Restoration</h3><p class="service-text">Lorem ipsum dolor sit amet,<br>consectetur adipiscing elit,send.</p></div>
  <div class="service" style="left:870px"><h3 class="service-title">Medical Massage</h3><p class="service-text">Lorem ipsum dolor sit amet,<br>consectetur adipiscing elit,send.</p></div>
</section>

<section class="section education">
  <h2 class="heading" style="top:62px">Our Education</h2>
  <div class="rule" style="top:121px"></div>
  <p class="body-copy" style="top:143px;line-height:31px">We are both Graduates of Venmora, school of massage therapy. We have continuing education in medical massage, myofacial<br>release, trigger point therapy, postural restoration, anatomy, and spontaneous muscle release. Lina is also a Certified Yoga<br>Instructor, which amplifies her experience with flexibility and strength as it pertains to each individual</p>
  <a class="read-more" style="top:266px">READ MORE</a>
</section>

<section class="section rates">
  <div class="abs" role="img" aria-label="Dim photo of a massage studio with treatment tables" style="inset:0"></div>
  <h2 class="heading" style="top:58px">Our Rate</h2>
  <div class="rule" style="top:116px;background:#8a8a8a"></div>
  <svg class="abs" style="left:0;top:0" width="1200" height="364" viewBox="0 0 1200 364" aria-hidden="true">
    <g fill="none" stroke-width="3">
      <circle cx="397" cy="233" r="66" stroke="#ffffff"/>
      <path d="M340 200 A66 66 0 0 0 420 295" stroke="var(--teal)" stroke-width="4"/>
      <circle cx="607" cy="233" r="66" stroke="#ffffff"/>
      <path d="M550 200 A66 66 0 0 0 630 295" stroke="var(--teal)" stroke-width="4"/>
      <circle cx="803" cy="233" r="66" stroke="#ffffff"/>
      <path d="M746 200 A66 66 0 0 0 826 295" stroke="var(--teal)" stroke-width="4"/>
    </g>
  </svg>
  <div class="rate-price" style="left:331px;top:209px">$ 75 / 60<br>Minutes</div>
  <div class="rate-price" style="left:541px;top:209px">$ 95 / 90<br>Minutes</div>
  <div class="rate-price" style="left:737px;top:209px">$ 120 / 120<br>Minutes</div>
</section>

<section class="section testimonials">
  <h2 class="heading" style="top:57px">Testimonials</h2>
  <div class="rule" style="top:116px"></div>
  <svg class="abs" style="left:0;top:0" width="300" height="346" viewBox="0 0 300 346" aria-hidden="true">
    <circle cx="187" cy="217" r="68" fill="none" stroke="var(--blue)" stroke-width="3"/>
    <circle cx="187" cy="217" r="61" fill="none" stroke="var(--blue)" stroke-width="1.5"/>
  </svg>
  <p class="date">December 17,<br>2015</p>
  <p class="quote">Lina and Paul at Kestrel Way are awesome! I recently had open heart surgery, and Lina worked on me to increase my range of motion while helping with the pinched nerve from my arm being in the same position for so long during my surgery. My wife drives a lot for work, and Paul has helped decrease her neck and lower back pain immensely. They are seriously the best therapists I have ever worked with</p>
  <p class="author">- Darcy T.</p>
</section>

<footer class="section site-footer">
  <svg class="abs" style="left:0;top:-27px" width="1200" height="180" viewBox="0 0 1200 180" aria-hidden="true">
    <circle cx="600" cy="27" r="27" fill="var(--blue-deep)"/>
    <circle cx="600" cy="27" r="22" fill="#ffffff"/>
    <path d="M593 29 l7 -7 l7 7 M593 36 l7 -7 l7 7" fill="none" stroke="var(--blue-deep)" stroke-width="2.6"/>
    <circle cx="550" cy="118" r="41" fill="none" stroke="#ffffff" stroke-width="2"/>
    <circle cx="550" cy="118" r="36" fill="none" stroke="#ffffff" stroke-width="1"/>
    <path d="M541 108 c2-2 4-2 5 0 l2 4 c1 2 0 3-2 4 c1 3 4 6 7 7 c1-2 2-3 4-2 l4 2 c2 1 2 3 0 5 c-3 3-7 3-11 0 c-4-3-8-7-10-11 c-2-4-1-7 1-9z" fill="#ffffff"/>
    <circle cx="650" cy="118" r="41" fill="none" stroke="#ffffff" stroke-width="2"/>
    <circle cx="650" cy="118" r="36" fill="none" stroke="#ffffff" stroke-width="1"/>
    <rect x="640" y="111" width="20" height="14" rx="1" fill="#ffffff"/>
    <path d="M640 112 l10 7 l10 -7" fill="none" stroke="var(--blue-deep)" stroke-width="1.6"/>
  </svg>
  <p class="contact-text" style="right:714px">(206) 555-0148</p>
  <p class="contact-text" style="left:710px">kestrelwaymassage@fernmail.net</p>
  <nav class="footer-nav">
    <span>Home</span><span class="sep">|</span><span>About us</span><span class="sep">|</span><span>Our Passion</span><span class="sep">|</span><span>Education</span><span class="sep">|</span><span>Testimonial</span><span class="sep">|</span><span>Contact Us</span>
  </nav>
  <div class="footer-rule"></div>
  <p class="copyright">© Kestrel Way mobile massage . 2015. All rights reserved.</p>
</footer>

</body>
</html>
```